Professional & attention grabbing.

A business card design, front and back. I already have a logo I will attach, but I am open to something new as well.
Things to include:
Name:
Title:
Phone:
Email:
Wanting something that is professional but attention grabbing.
Also we do a lot of work using drones on natural gas pipelines (leading the future)if you want to include any of that. I'm open to ideas.
Target Market(s)
Natural gas transmission industry / greenhouse gas mitigation industry
Industry/Entity Type
Business
Colors
Designer to choose colors to be used in the design.
Look and feel
Each slider illustrates characteristics of the customer's brand and the style your logo design should communicate.

```html
<!DOCTYPE html>
<html lang="en">
<head>
<meta charset="utf-8">
<title>Kestrel Inspections – Business Card</title>
<link href="https://fonts.googleapis.com/css2?family=Montserrat:wght@400;500;700;800&display=swap" rel="stylesheet">
<style>
  :root {
    --bg: #2b2b2b;
    --card-white: #ffffff;
    --brand-red: #bd2026;
    --brand-dark: #3a3a3c;
    --text-light: #ffffff;
  }
  * { margin: 0; padding: 0; box-sizing: border-box; }
  html, body { width: 1200px; height: 1000px; overflow: hidden; }
  body {
    background: var(--bg);
    font-family: 'Montserrat', sans-serif;
    position: relative;
  }
  .card {
    position: absolute;
    width: 540px;
    height: 310px;
    border-radius: 18px;
    overflow: hidden;
    box-shadow: 0 14px 30px rgba(0,0,0,0.45);
  }
  .card--front { left: 330px; top: 140px; background: var(--card-white); }
  .card--back { left: 330px; top: 550px; background: var(--brand-red); }

  .brand {
    position: absolute;
    display: flex;
    align-items: center;
    gap: 12px;
  }
  .brand__mark {
    width: 26px; height: 26px;
    background: var(--brand-red);
  }
  .brand__name {
    font-weight: 800;
    font-size: 30px;
    color: var(--brand-dark);
    letter-spacing: -0.5px;
    line-height: 1;
  }
  .card--front .brand { left: 50%; top: 50%; transform: translate(-50%, -50%); }
  .card--back .brand { left: 300px; top: 132px; }
  .card--back .brand__name { font-size: 26px; }

  .back-curves { position: absolute; inset: 0; }

  .contact {
    position: absolute;
    left: 48px;
    top: 148px;
    color: var(--text-light);
  }
  .contact__name { font-weight: 700; font-size: 20px; letter-spacing: 0.3px; }
  .contact__title { font-weight: 500; font-size: 13px; margin-top: 2px; }
  .contact__list { list-style: none; margin-top: 14px; }
  .contact__item {
    display: flex; align-items: center; gap: 10px;
    font-size: 14px; font-weight: 400; margin-top: 4px;
  }
  .contact__icon { width: 12px; height: 12px; fill: var(--text-light); }
</style>
</head>
<body>

  <section class="card card--front">
    <div class="brand">
      <span class="brand__mark"></span>
      <span class="brand__name">Kestrel Inspections</span>
    </div>
  </section>

  <section class="card card--back">
    <svg class="back-curves" viewBox="0 0 540 310" width="540" height="310" aria-hidden="true">
      <circle cx="452" cy="150" r="252" fill="var(--brand-dark)"/>
      <circle cx="468" cy="156" r="246" fill="var(--brand-red)"/>
      <circle cx="478" cy="158" r="236" fill="var(--card-white)"/>
    </svg>

    <div class="contact">
      <div class="contact__name">DANIEL REYES</div>
      <div class="contact__title">FOUNDER</div>
      <ul class="contact__list">
        <li class="contact__item">
          <svg class="contact__icon" viewBox="0 0 12 12"><path d="M1 4c0-2 2-3 5-3s5 1 5 3H8.5V3h-5v1zM2.5 5h7l1 5h-9z"/></svg>
          000 000 0000
        </li>
        <li class="contact__item">
          <svg class="contact__icon" viewBox="0 0 12 12"><path d="M0 2h12v8H0zM1 3l5 4 5-4z" fill-rule="evenodd"/></svg>
          info@kestrelmail.com
        </li>
      </ul>
    </div>

    <div class="brand">
      <span class="brand__mark"></span>
      <span class="brand__name">Kestrel Inspections</span>
    </div>
  </section>

</body>
</html>
```